Web Developer Needs a Business Card Design

I need a personal business card design that represents me as a web developer for potential employers. I would like the background to be a dark color on the front for contrast with my logo and name. The back will have all my information along with a smaller version of the logo. I want something with a modern look and feel, not too conservative. This will be used for potential employers and freelance work.

Industry/Entity Type

Business

Contact Information for Business Card

Front should have my logo and name. The back should have all my personal information which would include: name: Tom Varulek, phone: 570-614-3098, email: tomvarulek@quillbox.net, website url: www.tomvarulek.net, logo, web developer.

Font styles to use
Sans Serif

Requirements
Must have
• Must include my logo. The color palette base color will be the logo color.

```html
<!DOCTYPE html>
<html lang="en">
<head>
<meta charset="utf-8">
<title>Tom Varulek — Business Card</title>
<link rel="stylesheet" href="https://fonts.googleapis.com/css2?family=Raleway:wght@400;500&display=swap">
<style>
  :root {
    --page: #8a8b8b;
    --card-light: #e7e7e7;
    --teal: #4ec9ad;
    --dark: #2b2523;
    --dark-soft: #3a3330;
    --ink: #2a2a2a;
    --white: #f2f2f2;
    --shadow: 0 10px 18px rgba(0, 0, 0, 0.35);
  }
  * { margin: 0; padding: 0; box-sizing: border-box; }
  html, body { width: 1200px; height: 900px; overflow: hidden; }
  body {
    background: var(--page);
    font-family: "Raleway", sans-serif;
    position: relative;
  }
  .card {
    position: absolute;
    left: 320px;
    width: 560px;
    height: 320px;
    box-shadow: var(--shadow);
    overflow: hidden;
  }
  .card--front { top: 115px; background: var(--card-light); }
  .card--back { top: 470px; background: var(--dark); }

  .brand {
    position: absolute;
    display: flex;
    align-items: center;
    gap: 10px;
    color: var(--teal);
    font-weight: 500;
    white-space: nowrap;
    transform: translateX(-50%);
  }
  .brand__dot {
    border-radius: 50%;
    background: var(--teal);
    flex: none;
  }
  .card--front .brand { left: 280px; top: 140px; font-size: 30px; }
  .card--front .brand__dot { width: 26px; height: 26px; }
  .card--back .brand { left: 138px; top: 56px; font-size: 18px; }
  .card--back .brand__dot { width: 16px; height: 16px; }

  .back-art { position: absolute; inset: 0; }

  .identity {
    position: absolute;
    left: 138px;
    transform: translateX(-50%);
    text-align: center;
    color: var(--white);
    white-space: nowrap;
  }
  .identity__name {
    position: absolute;
    top: 140px;
    left: 0;
    transform: translateX(-50%);
    font-size: 25px;
    font-weight: 400;
    letter-spacing: 1.5px;
    text-transform: uppercase;
  }
  .identity__role {
    position: absolute;
    top: 182px;
    left: 0;
    transform: translateX(-50%);
    font-size: 13.5px;
    letter-spacing: 0.8px;
    color: #cfcfcf;
  }

  .contact {
    position: absolute;
    right: 30px;
    top: 155px;
    list-style: none;
    color: var(--ink);
    font-size: 14.5px;
    letter-spacing: 0.4px;
  }
  .contact__item {
    display: flex;
    justify-content: flex-end;
    align-items: center;
    gap: 18px;
    height: 23.5px;
  }
  .contact__icon { width: 14px; height: 14px; flex: none; }
</style>
</head>
<body>

  <section class="card card--front" aria-label="Card front">
    <div class="brand"><span class="brand__dot"></span>Tom Varulek</div>
  </section>

  <section class="card card--back" aria-label="Card back">
    <svg class="back-art" viewBox="0 0 560 320" width="560" height="320">
      <defs>
        <linearGradient id="workspace-tone" x1="0" y1="0" x2="1" y2="1">
          <stop offset="0" stop-color="#2a2220"/>
          <stop offset="0.6" stop-color="#221d1c"/>
          <stop offset="1" stop-color="#4a4a4c"/>
        </linearGradient>
      </defs>
      <rect width="560" height="320" fill="url(#workspace-tone)" role="img" aria-label="Dark photo of a desk workspace with a coffee cup and screen"/>
      <path d="M0,192 C80,250 200,272 300,188 S470,40 560,40 L560,320 L0,320 Z" fill="var(--white)"/>
      <path d="M0,204 C80,262 200,284 300,200 S470,52 560,52" fill="none" stroke="#111" stroke-width="3"/>
      <path d="M0,206 C80,264 200,286 300,202 S470,54 560,54 L560,320 L0,320 Z" fill="var(--teal)"/>
    </svg>

    <div class="brand"><span class="brand__dot"></span>Tom Varulek</div>

    <div class="identity">
      <h1 class="identity__name">Tom Varulek</h1>
      <p class="identity__role">Front-End Developer</p>
    </div>

    <ul class="contact">
      <li class="contact__item">570-614-3098
        <svg class="contact__icon" viewBox="0 0 16 16"><path d="M3 1l3 0 1 4-2 1.5c1 2 2.5 3.5 4.5 4.5L11 9l4 1 0 3c0 1-1 2-2 2C7 15 1 9 1 3c0-1 1-2 2-2z" fill="#222"/></svg>
      </li>
      <li class="contact__item">tomvarulek@quillbox.net
        <svg class="contact__icon" viewBox="0 0 16 16"><rect x="1" y="3.5" width="14" height="9" fill="#222"/><path d="M1.5 4l6.5 5 6.5-5" fill="none" stroke="#4ec9ad" stroke-width="1.2"/></svg>
      </li>
      <li class="contact__item">www.tomvarulek.net
        <svg class="contact__icon" viewBox="0 0 16 16"><circle cx="8" cy="8" r="7" fill="#222"/><path d="M1 8h14M8 1c-3 3-3 11 0 14M8 1c3 3 3 11 0 14" fill="none" stroke="#4ec9ad" stroke-width="1"/></svg>
      </li>
      <li class="contact__item">@tomvarulek.net
        <svg class="contact__icon" viewBox="0 0 16 16"><circle cx="8" cy="8" r="6" fill="#222"/></svg>
      </li>
      <li class="contact__item">tomvarulek.net
        <svg class="contact__icon" viewBox="0 0 16 16"><rect x="2" y="2" width="12" height="12" fill="#222"/></svg>
      </li>
      <li class="contact__item">tomvarulek.net
        <svg class="contact__icon" viewBox="0 0 16 16"><circle cx="8" cy="8" r="6" fill="#222"/></svg>
      </li>
    </ul>
  </section>

</body>
</html>
```